Business card for medical clinic

I need an upmarket, modern medical/health business card for my clinic

Contact Information for Business Card

name, address, email, qr code

```html
<!DOCTYPE html>
<html lang="en">
<head>
<meta charset="utf-8">
<title>Meridian Care Clinic – Business Card</title>
<link href="https://fonts.googleapis.com/css2?family=Poppins:wght@300;400;500;600&display=swap" rel="stylesheet">
<style>
  :root {
    --stage: #232324;
    --card-dark: #1f1f22;
    --brand-blue: #2aa3dc;
    --brand-blue-deep: #1678b4;
    --silver: #e9eef4;
    --text-light: #f2f4f7;
  }
  * { box-sizing: border-box; margin: 0; padding: 0; }
  html, body {
    width: 1200px; height: 780px; overflow: hidden;
    background: var(--stage);
    font-family: "Poppins", sans-serif;
  }
  .stage {
    position: relative; width: 1200px; height: 780px;
    display: flex; align-items: center; justify-content: center; gap: 40px;
  }
  .card {
    position: relative; width: 540px; height: 309px;
    overflow: hidden; border-radius: 3px;
    box-shadow: 0 18px 40px rgba(0,0,0,.55);
  }
  /* Front */
  .card--front { background: var(--card-dark); color: var(--text-light); }
  .card__band { position: absolute; inset: 0; width: 100%; height: 100%; }
  .brand {
    position: absolute; left: 38px; top: 40px;
    display: flex; align-items: center; gap: 12px;
  }
  .brand__dot {
    width: 26px; height: 26px; border-radius: 50%;
    background: var(--brand-blue);
  }
  .brand__name {
    font-weight: 500; font-size: 17px; letter-spacing: 2px;
    color: var(--brand-blue); text-transform: uppercase;
  }
  .person { position: absolute; left: 38px; top: 116px; }
  .person__name { font-size: 34px; line-height: 1.1; color: var(--brand-blue); }
  .person__first { font-weight: 600; }
  .person__last { font-weight: 300; }
  .person__title { margin-top: 4px; font-size: 15px; font-weight: 400; color: var(--text-light); }
  .divider {
    position: absolute; left: 292px; top: 104px;
    width: 1px; height: 80px; background: var(--brand-blue);
  }
  .contacts {
    position: absolute; left: 312px; top: 104px;
    list-style: none; display: flex; flex-direction: column; gap: 9px;
    font-size: 12.5px; color: var(--text-light);
  }
  .contacts__item { display: flex; align-items: center; gap: 8px; }
  .contacts__icon { width: 16px; height: 16px; flex: none; }
  .address {
    position: absolute; right: 24px; bottom: 12px;
    font-size: 12.5px; color: #ffffff; letter-spacing: .2px;
  }
  /* Back */
  .card--back {
    background: radial-gradient(ellipse at 40% 55%, #2ea9df 0%, var(--brand-blue) 60%, #2496cc 100%);
    display: flex; align-items: center; justify-content: center; gap: 18px;
  }
  .card--back .brand__dot { width: 46px; height: 46px; background: #bfe6f7; }
  .card--back .brand__name { font-size: 27px; letter-spacing: 3px; color: #d6f0fb; }
</style>
</head>
<body>
<main class="stage">

  <section class="card card--front" aria-label="Business card front">
    <svg class="card__band" viewBox="0 0 540 309" preserveAspectRatio="none" aria-hidden="true">
      <defs>
        <linearGradient id="bandFill" x1="0" y1="0" x2="1" y2="0">
          <stop offset="0" stop-color="#e9eef4"/>
          <stop offset=".12" stop-color="#1678b4"/>
          <stop offset=".6" stop-color="#2aa3dc"/>
          <stop offset=".9" stop-color="#1e8ccb"/>
          <stop offset="1" stop-color="#e9eef4"/>
        </linearGradient>
      </defs>
      <path d="M0,309 L0,282 Q300,270 540,212 L540,309 Z" fill="url(#bandFill)"/>
      <path d="M18,274 Q300,258 532,200" fill="none" stroke="#2aa3dc" stroke-width="2.5"/>
    </svg>

    <div class="brand">
      <span class="brand__dot"></span>
      <span class="brand__name">Meridian Care Clinic</span>
    </div>

    <div class="person">
      <p class="person__name"><span class="person__first">Dana</span> <span class="person__last">Morrow</span></p>
      <p class="person__title">Founder &amp; CEO</p>
    </div>

    <span class="divider"></span>

    <ul class="contacts">
      <li class="contacts__item">
        <svg class="contacts__icon" viewBox="0 0 16 16" aria-hidden="true"><path d="M4 1.5l2.2 3-1.3 1.6a8 8 0 0 0 5 5l1.6-1.3 3 2.2-1.2 2.3C7.6 14 2 8.4 1.7 2.7z" fill="#2aa3dc"/></svg>
        (555) 014-2290
      </li>
      <li class="contacts__item">
        <svg class="contacts__icon" viewBox="0 0 16 16" aria-hidden="true"><rect x="1.5" y="3.5" width="13" height="9" rx="1" fill="none" stroke="#2aa3dc" stroke-width="1.4"/><path d="M2 4l6 5 6-5" fill="none" stroke="#2aa3dc" stroke-width="1.4"/></svg>
        hello@meridiancare.example
      </li>
      <li class="contacts__item">
        <svg class="contacts__icon" viewBox="0 0 16 16" aria-hidden="true"><circle cx="8" cy="8" r="6.3" fill="none" stroke="#2aa3dc" stroke-width="1.4"/><path d="M1.7 8h12.6M8 1.7c-3 3.5-3 9 0 12.6M8 1.7c3 3.5 3 9 0 12.6" fill="none" stroke="#2aa3dc" stroke-width="1.1"/></svg>
        www.meridiancare.example
      </li>
    </ul>

    <p class="address">418 Linden Ave. Suite 120 Brookfield, TX 75011</p>
  </section>

  <section class="card card--back" aria-label="Business card back">
    <span class="brand__dot"></span>
    <span class="brand__name">Meridian Care Clinic</span>
  </section>

</main>
</body>
</html>
```